Velmaro Partners Logo and Business Card Design

We already have the rough logo shape (however please make the lines on the logo much thicker so a dark background is not required to see it) . see photos uploaded.
It needs to be refined with color and digitized and then have a front and back business card layout done.
The services are high vibration healing support through a therapy and feng shui service offering. We want people to Feel Happiness, Feel Prosperity and Feel Peace. (the back of the card would have these phrases on it) So a warm, calm and peaceful feeling card.
We would like the card to use the logo provided (with thicker lines and color added) but below the graphic please use the name "Velmaro Partners" NOT Velmaro.
We also would like to use the colors in the colorized matrix shown in photos (gold and purple) but on the lighter side. Thanks for your time!

Front of Card should include: Logo, with Company Name: Velmaro Partners as part of logo, Name: Tomas Brekke email: tomas@velmaro.example web: www.velmaro.example mobile: 555.018.2264 at bottom of front list Family Constellation | Feng Shui

Back of Card should have the logo and the following listed vertically:

PERSONAL | BUSINESS (Larger size then smaller bullet items below)
*Find Happiness
*Find Prosperity
*Find Peace

Target Market(s)

Target market is both business and personal

Contact Information for Business Card

Front of Card should include: Logo, with Company Name: Velmaro Partners as part of logo, Name: Tomas Brekke email: tomas@velmaro.example web: www.velmaro.example mobile: 555.018.2264 at bottom of front list Family Constellation | Feng Shui ++++ Back of Card should have the logo and the following listed vertically: PERSONAL | BUSINESS (Larger size then smaller bullet items below) *Find Happiness *Find Prosperity *Find Peace

Font styles to use
Sans Serif

Colors

Designer to choose colors to be used in the design.

Requirements
Nice to have
• Nice light contrast color for the back of card background
Should not have
• No dark colored background on Card.

```html
<!DOCTYPE html>
<html lang="en">
<head>
<meta charset="UTF-8">
<title>Velmaro Partners – Business Card</title>
<link rel="stylesheet" href="https://fonts.googleapis.com/css2?family=Montserrat:wght@400;500;600;700&display=swap">
<style>
  :root {
    --gold: #d9a928;
    --gold-light: #ecc838;
    --gold-deep: #c8951c;
    --purple: #5b3a98;
    --purple-soft: #7a64b0;
    --ink: #1f1f1f;
    --card: #ffffff;
    --backdrop: #ebe6de;
  }
  * { box-sizing: border-box; margin: 0; padding: 0; }
  html, body { width: 900px; height: 1200px; overflow: hidden; }
  body {
    background: var(--backdrop);
    font-family: "Montserrat", sans-serif;
    color: var(--ink);
    position: relative;
  }
  .card {
    position: absolute;
    left: 80px;
    width: 742px;
    height: 440px;
    background: var(--card);
    border-radius: 28px;
    overflow: hidden;
    box-shadow: 0 6px 14px rgba(0,0,0,0.25);
  }
  .card--front { top: 132px; }
  .card--back { top: 639px; }

  /* brand lockup */
  .brand {
    position: absolute;
    text-align: center;
    color: var(--gold);
    font-weight: 600;
  }
  .brand__mark {
    display: block;
    margin: 0 auto;
    border: 9px solid var(--purple);
    border-radius: 50%;
  }
  .brand__name {
    display: block;
    text-transform: uppercase;
    line-height: 1.1;
  }
  .card--front .brand { left: 470px; top: 60px; width: 240px; }
  .card--front .brand__mark { width: 92px; height: 92px; margin-bottom: 26px; }
  .card--front .brand__name { font-size: 34px; letter-spacing: 1px; }
  .card--front .brand__name--sub { font-size: 19px; letter-spacing: 6px; margin-top: 6px; }

  .card--back .brand { left: 221px; top: 60px; width: 300px; }
  .card--back .brand__mark { width: 90px; height: 90px; margin-bottom: 80px; }
  .card--back .brand__name { font-size: 46px; letter-spacing: 1px; }
  .card--back .brand__name--sub { font-size: 22px; letter-spacing: 8px; margin-top: 4px; }

  /* front contact block */
  .person {
    position: absolute;
    left: 29px;
    top: 286px;
    font-size: 25px;
    font-weight: 700;
    color: var(--gold);
    letter-spacing: 0.5px;
  }
  .divider {
    position: absolute;
    left: 29px;
    top: 323px;
    width: 687px;
    height: 1px;
    background: var(--gold);
  }
  .contacts {
    position: absolute;
    left: 30px;
    top: 330px;
    list-style: none;
    font-size: 17px;
    font-weight: 500;
  }
  .contacts li {
    display: flex;
    align-items: center;
    height: 24px;
  }
  .contacts svg { width: 14px; height: 14px; margin-right: 13px; fill: var(--gold); }

  .footer-band {
    position: absolute;
    left: 0;
    bottom: 0;
    width: 742px;
    height: 46px;
  }
  .services {
    position: absolute;
    right: 20px;
    bottom: 12px;
    font-size: 17px;
    font-weight: 500;
  }
  .services span { margin: 0 8px; }

  /* back */
  .audience {
    position: absolute;
    left: 0;
    top: 340px;
    width: 742px;
    height: 31px;
    background: linear-gradient(90deg, var(--gold-deep), var(--gold-light));
    text-align: center;
    font-size: 20px;
    font-weight: 700;
    letter-spacing: 2.5px;
    line-height: 31px;
    text-transform: uppercase;
  }
  .audience span { margin: 0 12px; }
  .promises {
    position: absolute;
    left: 0;
    top: 390px;
    width: 742px;
    text-align: center;
    font-size: 18px;
    font-weight: 500;
  }
  .promises .dot { color: var(--gold); margin: 0 8px; }
</style>
</head>
<body>

  <section class="card card--front" aria-label="Business card front">
    <div class="brand">
      <span class="brand__mark"></span>
      <span class="brand__name">Velmaro</span>
      <span class="brand__name brand__name--sub">Partners</span>
    </div>

    <h1 class="person">TOMAS BREKKE</h1>
    <div class="divider"></div>

    <ul class="contacts">
      <li>
        <svg viewBox="0 0 16 16" aria-hidden="true"><path d="M1 6c0-2 3-3 7-3s7 1 7 3v1h-3V5.5H4V7H1zM3 8h10l1 6H2z"/></svg>
        555.018.2264
      </li>
      <li>
        <svg viewBox="0 0 16 16" aria-hidden="true"><path d="M1 3h14v10H1zM2 4l6 5 6-5z" fill-rule="evenodd"/></svg>
        tomas@velmaro.example
      </li>
      <li>
        <svg viewBox="0 0 16 16" aria-hidden="true"><circle cx="8" cy="8" r="7"/></svg>
        www.velmaro.example
      </li>
    </ul>

    <svg class="footer-band" viewBox="0 0 742 46" aria-hidden="true">
      <defs>
        <linearGradient id="bandGold" x1="0" x2="1">
          <stop offset="0" stop-color="#d7a522"/>
          <stop offset="1" stop-color="#ebc73a"/>
        </linearGradient>
      </defs>
      <polygon points="0,14 391,14 380,26 0,26" fill="#7a64b0"/>
      <path d="M400,32 L410,14 Q415,0 430,0 L742,0 L742,46 L0,46 L0,40 L385,40 Q396,40 400,32 Z" fill="url(#bandGold)"/>
    </svg>
    <p class="services">Family Constellation<span>|</span>Feng Shui</p>
  </section>

  <section class="card card--back" aria-label="Business card back">
    <div class="brand">
      <span class="brand__mark"></span>
      <span class="brand__name">Velmaro</span>
      <span class="brand__name brand__name--sub">Partners</span>
    </div>

    <p class="audience">Business<span>|</span>Personal</p>
    <p class="promises">
      Find Happiness<span class="dot">•</span>Find Prosperity<span class="dot">•</span>Find Peace
    </p>
  </section>

</body>
</html>
```